Logo, Web and Mobile Designs for enterprise social media platform

All the details are in the attached document, please start reading the scope document first which explains what is this project about and the details about the needed deliverables, after that please read the UI_Requirements document which will detail what is expected regarding the coded web version since this is a coded contest, it is very important that you meet the UI requirements or suggest something else but we will need to agree first before working on the coded version

Good Luck

Target Market(s)

Enterprise Social Media

Industry/Entity Type

Media

Coding

Coded - Design and coding required

Number of Pages Required

5+ page

Font styles to use
Sans Serif

Requirements
Must have
• All the must haves are listed in the scope document so please check before you start

```html
<!DOCTYPE html>
<html lang="en">
<head>
<meta charset="utf-8">
<title>Taskora Sign In</title>
<link rel="stylesheet" href="https://fonts.googleapis.com/css2?family=Roboto:wght@400;500&family=Open+Sans:wght@400&display=swap">
<style>
  :root {
    --page-bg: #ecebf0;
    --screen-bg: #f6f6f6;
    --header-bg: #fbfbfb;
    --rule: #e2e2e2;
    --heading: #555555;
    --label: #5e5e5e;
    --field-bg: #ffffff;
    --field-border: #e4e4e4;
    --icon: #9a9a9a;
    --brand: #2a9fd0;
    --brand-dot: #f0a81c;
    --sign-in: #e89100;
    --register: #24a0cf;
    --footer-bg: #393939;
    --footer-text: #ffffff;
  }
  * { box-sizing: border-box; margin: 0; padding: 0; }
  html, body { width: 682px; height: 1200px; overflow: hidden; }
  body { background: var(--page-bg); font-family: "Roboto", Arial, sans-serif; position: relative; }

  .app-screen {
    position: absolute; left: 0; top: 97px; width: 682px; height: 1006px;
    background: linear-gradient(160deg, #f9f9f9 0%, #f2f2f2 50%, #f7f7f7 100%);
  }

  .top-bar {
    position: absolute; left: 0; top: 0; width: 682px; height: 134px;
    background: var(--header-bg); border-bottom: 2px solid var(--rule);
  }
  .top-bar__home, .top-bar__menu {
    position: absolute; top: 0; width: 122px; height: 132px;
    display: flex; align-items: center; justify-content: center;
  }
  .top-bar__home { left: 0; border-right: 1px solid var(--rule); }
  .top-bar__menu { right: 0; border-left: 1px solid var(--rule); }
  .brand {
    position: absolute; left: 122px; right: 122px; top: 0; height: 132px;
    display: flex; align-items: center; justify-content: center; gap: 12px;
  }
  .brand__dot { width: 40px; height: 40px; border-radius: 50%; background: var(--brand-dot); }
  .brand__name { font-size: 46px; font-weight: 400; color: var(--brand); letter-spacing: 0.5px; }

  .section-title {
    position: absolute; left: 0; width: 682px; height: 100px;
    border-bottom: 1px solid var(--rule);
    padding-left: 29px; display: flex; align-items: center;
    font-size: 30px; font-weight: 400; color: var(--heading); letter-spacing: 1.2px;
  }
  .section-title--signin { top: 134px; }
  .section-title--signup { top: 548px; border-top: 1px solid var(--rule); }

  .field-label {
    position: absolute; font-size: 20px; color: var(--label);
  }
  .field-label span { font-size: 15px; margin-left: 4px; }
  .field {
    position: absolute; height: 65px; background: var(--field-bg);
    border: 1px solid var(--field-border); border-radius: 3px;
  }
  .field svg { position: absolute; right: 20px; top: 50%; transform: translateY(-50%); }

  .options-row { position: absolute; top: 453px; left: 0; width: 682px; height: 54px; }
  .remember {
    position: absolute; left: 101px; top: 0; height: 54px;
    display: flex; align-items: center; gap: 8px;
    font-family: "Open Sans", Arial, sans-serif; font-size: 19px; color: var(--label);
  }
  .remember__radio { width: 21px; height: 21px; border: 2px solid #6a6a6a; border-radius: 50%; }
  .forgot {
    position: absolute; left: 300px; top: 0; height: 54px; line-height: 54px;
    font-family: "Open Sans", Arial, sans-serif; font-size: 19px; color: var(--label);
    text-decoration: underline; text-underline-offset: 3px;
  }
  .btn {
    position: absolute; border-radius: 3px; color: #fff;
    font-size: 20px; font-weight: 400; display: flex; align-items: center; justify-content: center;
  }
  .btn--sign-in { left: 476px; top: 453px; width: 160px; height: 54px; background: var(--sign-in); }
  .btn--register { left: 466px; top: 764px; width: 174px; height: 56px; background: var(--register); }

  .site-footer {
    position: absolute; left: 0; top: 855px; width: 682px; height: 151px;
    background: var(--footer-bg); color: var(--footer-text);
    font-family: "Open Sans", Arial, sans-serif; text-align: center;
  }
  .site-footer__links { position: absolute; top: 44px; width: 100%; font-size: 18px; }
  .site-footer__copy { position: absolute; top: 82px; width: 100%; font-size: 20px; }
</style>
</head>
<body>
  <main class="app-screen">
    <header class="top-bar">
      <div class="top-bar__home">
        <svg width="30" height="26" viewBox="0 0 30 26" aria-label="Home">
          <path d="M15 2 L2 13 H6 V24 H12 V17 H18 V24 H24 V13 H28 Z" fill="#6a6a6a"/>
        </svg>
      </div>
      <div class="brand">
        <div class="brand__dot"></div>
        <div class="brand__name">Taskora</div>
      </div>
      <div class="top-bar__menu">
        <svg width="30" height="26" viewBox="0 0 30 26" aria-label="Menu">
          <rect x="0" y="2" width="30" height="4" fill="#6a6a6a"/>
          <rect x="0" y="11" width="30" height="4" fill="#6a6a6a"/>
          <rect x="0" y="20" width="30" height="4" fill="#6a6a6a"/>
        </svg>
      </div>
    </header>

    <h1 class="section-title section-title--signin">TASKORA SIGN IN</h1>

    <label class="field-label" style="left:30px; top:296px;">User Name<span>*</span></label>
    <div class="field" style="left:172px; top:276px; width:464px;">
      <svg width="18" height="20" viewBox="0 0 18 20"><circle cx="9" cy="6" r="5" fill="var(--icon)"/><path d="M0 20 Q0 12 9 12 Q18 12 18 20 Z" fill="var(--icon)"/></svg>
    </div>

    <label class="field-label" style="left:44px; top:384px;">Password<span>*</span></label>
    <div class="field" style="left:172px; top:364px; width:464px;">
      <svg width="22" height="22" viewBox="0 0 22 22" fill="var(--icon)">
        <circle cx="11" cy="2.5" r="2.2"/><circle cx="17" cy="5" r="2"/><circle cx="19.5" cy="11" r="1.8"/>
        <circle cx="17" cy="17" r="1.6"/><circle cx="11" cy="19.5" r="1.5"/><circle cx="5" cy="17" r="1.4"/>
        <circle cx="2.5" cy="11" r="1.3"/><circle cx="5" cy="5" r="1.2"/>
      </svg>
    </div>

    <div class="options-row">
      <div class="remember"><span class="remember__radio"></span>Remember me</div>
      <span class="forgot">Forgot Password</span>
    </div>
    <div class="btn btn--sign-in">SIGN IN</div>

    <h2 class="section-title section-title--signup">TASKORA SIGN UP</h2>

    <label class="field-label" style="left:34px; top:700px;">E - Mail<span>*</span></label>
    <div class="field" style="left:178px; top:680px; width:462px; height:64px;">
      <svg width="22" height="17" viewBox="0 0 22 17"><rect x="1" y="1" width="20" height="15" rx="2" fill="none" stroke="var(--icon)" stroke-width="1.6"/><path d="M1 3 L11 10 L21 3" fill="none" stroke="var(--icon)" stroke-width="1.6"/></svg>
    </div>
    <div class="btn btn--register">REGISTER</div>

    <footer class="site-footer">
      <div class="site-footer__links">Terms &amp; Conditions Privacy Policy</div>
      <div class="site-footer__copy">Copyright 2015&nbsp; taskora., All Rights Reserved.</div>
    </footer>
  </main>
</body>
</html>
```